Verdant Systems Business Card

want the back of card to be blue- with the logo in the center
front of card- info plus logo (info being mailing address, email address, and website address )
4 different names with titles to have on cards
1) Calvin Borsted - Owner
2) Naomi Trelvik- Customer Relationship Specialist
3) Felix Andrade- Vice President of Sales
4) Owen Markby- Chief Technology Officer

Target Market(s)

tech company in the government/probation office industry

Industry/Entity Type

Government Office

Contact Information for Business Card

1) Calvin Borsted - Owner

Colors
0355a3
ffffff

Requirements
Must have
• back side should be blue, with the logo placed in the center
• front side needs to include both the logo, as well as company info (info should include website address, email address, and mailing address)

```html
<!DOCTYPE html>
<html lang="en">
<head>
<meta charset="utf-8">
<title>Verdant Systems Business Card</title>
<link href="https://fonts.googleapis.com/css2?family=Open+Sans:wght@400;600;700&family=Roboto:wght@700&display=swap" rel="stylesheet">
<style>
  :root {
    --backdrop: #c4c8cc;
    --navy: #1b2d52;
    --white: #ffffff;
    --ink: #333a44;
    --shadow: rgba(0, 0, 0, 0.35);
  }
  * { margin: 0; padding: 0; box-sizing: border-box; }
  html, body {
    width: 1200px; height: 900px; overflow: hidden;
    background: var(--backdrop);
    font-family: "Open Sans", Arial, sans-serif;
  }
  .board { position: relative; width: 1200px; height: 900px; }

  .card-front {
    position: absolute; left: 56px; width: 453px; height: 258px;
    background: var(--white); border-radius: 22px; overflow: hidden;
    box-shadow: 0 5px 9px var(--shadow);
  }
  .card-front.calvin { top: 36px; }
  .card-front.naomi  { top: 328px; }
  .card-front.felix  { top: 619px; }

  .brand {
    position: absolute; left: 0; right: 0; top: 58px;
    display: flex; justify-content: center; align-items: center; gap: 8px;
    color: var(--navy); font-weight: 700; font-size: 24px; letter-spacing: 0.5px;
  }
  .brand-mark { width: 14px; height: 14px; background: var(--navy); }

  .person {
    position: absolute; right: 238px; top: 156px; text-align: right;
  }
  .person-name { color: var(--navy); font-weight: 700; font-size: 14px; line-height: 18px; }
  .person-title { color: var(--ink); font-size: 11.5px; line-height: 16px; }

  .divider {
    position: absolute; left: 226px; top: 148px; width: 1px; height: 53px;
    background: var(--navy);
  }
  .contact { position: absolute; left: 238px; top: 145px; list-style: none; }
  .contact li {
    display: flex; align-items: center; gap: 7px;
    color: var(--ink); font-size: 11.5px; line-height: 14.7px;
  }
  .contact svg { width: 8px; height: 8px; fill: var(--navy); flex: none; }

  .address-band {
    position: absolute; left: 0; right: 0; top: 224px; height: 23px;
    background: var(--navy); color: var(--white);
    font-size: 11.5px; line-height: 23px; text-align: center;
  }

  .card-back {
    position: absolute; left: 584px; top: 296px; width: 567px; height: 323px;
    background: var(--navy); border-radius: 24px;
    box-shadow: 0 5px 9px var(--shadow);
    display: flex; justify-content: center; align-items: center; gap: 14px;
  }
  .card-back .brand-mark { width: 24px; height: 24px; background: var(--white); }
  .card-back .brand-name {
    color: var(--white); font-weight: 700; font-size: 40px; letter-spacing: 1px;
  }

  .designer-note {
    position: absolute; left: 575px; top: 720px; width: 600px;
    color: var(--navy); font-family: "Roboto", Arial, sans-serif;
    font-weight: 700; font-size: 21.5px; line-height: 27px;
  }
</style>
</head>
<body>
<svg width="0" height="0" style="position:absolute">
  <defs>
    <symbol id="icon-phone" viewBox="0 0 10 10"><path d="M2 0.5 L3.6 2.6 L2.8 3.6 C3.4 5 5 6.6 6.4 7.2 L7.4 6.4 L9.5 8 L8.3 9.5 C4.5 9.2 0.8 5.5 0.5 1.7 Z"/></symbol>
    <symbol id="icon-mobile" viewBox="0 0 10 10"><path d="M2.5 0 H7.5 V10 H2.5 Z M3.5 1 V8 H6.5 V1 Z"/></symbol>
    <symbol id="icon-mail" viewBox="0 0 10 10"><path d="M0 1.5 H10 V8.5 H0 Z M1 2.5 L5 5.5 L9 2.5 V2.5 Z" fill-rule="evenodd"/></symbol>
    <symbol id="icon-globe" viewBox="0 0 10 10"><circle cx="5" cy="5" r="5"/><path d="M2 3 Q4 2 4.5 4 Q3 6 5 7.5 Q3 9 2 6 Z M6 1.5 Q8 3 7 5 Q6 4 6 1.5 Z" fill="#ffffff"/></symbol>
  </defs>
</svg>

<main class="board">
  <section class="card-front calvin">
    <div class="brand"><span class="brand-mark"></span><span class="brand-name">Verdant Systems</span></div>
    <div class="person"><p class="person-name">Calvin Borsted</p><p class="person-title">Owner</p></div>
    <div class="divider"></div>
    <ul class="contact">
      <li><svg><use href="#icon-phone"/></svg>555-214-7730</li>
      <li><svg><use href="#icon-mobile"/></svg>555-308-4126(office)</li>
      <li><svg><use href="#icon-mail"/></svg>hello@verdantsysco.com</li>
      <li><svg><use href="#icon-globe"/></svg>www.verdantsysco.com</li>
    </ul>
    <div class="address-band">Harlow Junction Ellmore Crossing, 2740</div>
  </section>

  <section class="card-front naomi">
    <div class="brand"><span class="brand-mark"></span><span class="brand-name">Verdant Systems</span></div>
    <div class="person"><p class="person-name">Naomi Trelvik</p><p class="person-title">Customer Relationship Specialist</p></div>
    <div class="divider"></div>
    <ul class="contact">
      <li><svg><use href="#icon-phone"/></svg>555-214-7730</li>
      <li><svg><use href="#icon-mobile"/></svg>555-308-4126(office)</li>
      <li><svg><use href="#icon-mail"/></svg>hello@verdantsysco.com</li>
      <li><svg><use href="#icon-globe"/></svg>www.verdantsysco.com</li>
    </ul>
    <div class="address-band">Harlow Junction Ellmore Crossing, 2740</div>
  </section>

  <section class="card-front felix">
    <div class="brand"><span class="brand-mark"></span><span class="brand-name">Verdant Systems</span></div>
    <div class="person"><p class="person-name">Felix Andrade</p><p class="person-title">Vice President of Sales</p></div>
    <div class="divider"></div>
    <ul class="contact">
      <li><svg><use href="#icon-phone"/></svg>555-214-7730</li>
      <li><svg><use href="#icon-mobile"/></svg>555-308-4126(office)</li>
      <li><svg><use href="#icon-mail"/></svg>hello@verdantsysco.com</li>
      <li><svg><use href="#icon-globe"/></svg>www.verdantsysco.com</li>
    </ul>
    <div class="address-band">Harlow Junction Ellmore Crossing, 2740</div>
  </section>

  <section class="card-back">
    <span class="brand-mark"></span><span class="brand-name">Verdant Systems</span>
  </section>

  <p class="designer-note">I have made this card by using 3 different name . If you want i will make the card 4 different name and provide you all editable and print ready file.</p>
</main>
</body>
</html>
```